Cedarvale Ridge College

We are looking to update our current webpage at www.cedarvaleridge.ca. We would like to make it modern, fresh and appealing to students. We want to keep our logo the same with the logo colours blended in as the primary colours and focus. We are open to reconfiguring content as well.
Reason: Hi, In the next 3 days we will have narrowed our search to 3 designs and will make a choice before the final deadline...
College

```html
<!DOCTYPE html>
<html lang="en">
<head>
<meta charset="utf-8">
<title>Cedarvale Ridge College</title>
<link rel="stylesheet" href="https://fonts.googleapis.com/css2?family=Cinzel:wght@400;700&family=Lato:wght@400;700&family=Lora:ital@0;1&display=swap">
<style>
:root{
  --navy:#1b2b63;
  --navy-dark:#132049;
  --green:#0f6e4f;
  --green-dark:#0a573e;
  --text:#333;
  --muted:#666;
  --campus-bg:#f1f2f2;
  --footer:#262626;
  --footer-bar:#1c1c1c;
  --footer-text:#dcdcdc;
  --line:#dcdcdc;
}
*{margin:0;padding:0;box-sizing:border-box}
html,body{width:758px;height:1200px;overflow:hidden}
body{position:relative;font-family:"Lato",sans-serif;color:var(--text);background:#fff}
.abs{position:absolute}

/* header */
.site-header{left:0;top:0;width:758px;height:75px;background:linear-gradient(#fff,#ededed);border-top:2px solid var(--navy)}
.utility-tabs{left:412px;top:0;width:263px;height:20px;background:var(--navy);border-radius:0 0 8px 8px;display:flex;justify-content:space-around;align-items:center}
.utility-tabs a{color:#fff;font-size:9px;font-weight:700;text-decoration:none;letter-spacing:.2px}
.brand{left:85px;top:12px;color:var(--navy);font-family:"Cinzel",serif;font-weight:700;font-size:15px;line-height:16px;width:150px}
.social-dots{left:460px;top:40px;display:flex;gap:8px}
.social-dots span{width:17px;height:17px;border-radius:50%;background:#9a9a9a;display:block}
.search{left:553px;top:38px;width:122px;height:20px;display:flex}
.search input{width:99px;height:20px;border:1px solid #ccc;font-size:8px;padding-left:6px;font-style:italic;font-family:"Lato",sans-serif;background:#fff}
.search button{width:23px;height:20px;border:0;background:var(--navy);display:flex;align-items:center;justify-content:center}

/* nav */
.main-nav{left:0;top:75px;width:758px;height:30px;background:linear-gradient(var(--green),var(--green-dark))}
.main-nav-links{position:absolute;left:83px;top:6px;width:593px;height:18px;display:flex;align-items:center}
.main-nav-links a{flex:auto;text-align:center;white-space:nowrap;color:#fff;font-family:"Lora",serif;font-size:9.6px;line-height:18px;text-decoration:none;padding:0 3px;border-right:1px solid rgba(255,255,255,.25)}
.main-nav-links a:last-child{border-right:0}
.main-nav-links a.active{flex:none;width:38px;background:var(--navy);border-radius:9px;border-right:0;margin-right:4px}

/* hero */
.hero{left:0;top:105px;width:758px;height:227px;background:linear-gradient(180deg,#0f1a4a 0%,#23306b 45%,#5e4a3a 75%,#c67a2e 100%)}
.hero-arrow{top:218px;width:38px;height:25px;background:rgba(60,60,60,.85);display:flex;align-items:center;justify-content:center}
.hero-caption{left:0;top:332px;width:758px;height:26px;background:#5b586a;color:#fff;font-family:"Lora",serif;font-style:italic;font-size:12px;text-align:center;line-height:26px}

/* headings */
.heading{font-family:"Cinzel",serif;font-size:15px;color:var(--navy);letter-spacing:.3px;white-space:nowrap}
.heading em{font-style:normal;color:var(--green)}
.heading-rule{height:1px;background:linear-gradient(90deg,#bbb,transparent)}

/* about */
.about-copy{left:84px;top:409px;width:334px;font-size:8px;line-height:12px;color:var(--text)}
.about-copy p{margin-bottom:7px}
.read-more-link{left:84px;top:516px;font-size:8px;font-style:italic;color:var(--navy);text-decoration:underline}
.divider{left:443px;top:376px;width:1px;height:150px;background:var(--line)}
.video{left:469px;top:410px;width:206px;height:114px;background:linear-gradient(#8a8a6e,#3b3e55)}
.video-bar{left:469px;top:505px;width:206px;height:19px;background:#222;display:flex;align-items:center;padding:0 8px;gap:8px}
.video-bar .track{flex:1;height:3px;background:#555;position:relative}
.video-bar .track i{position:absolute;left:0;top:0;height:3px;width:72%;background:#3aa3d9}

/* campus */
.campus{left:0;top:545px;width:758px;height:273px;background:var(--campus-bg)}
.campus-title{left:0;top:560px;width:758px;display:flex;align-items:center;justify-content:center;gap:10px}
.campus-title .line{width:190px;height:3px;border-top:1px solid #ccc;border-bottom:1px solid #ccc}
.card{top:593px;width:179px;height:200px;background:#fff;border:1px solid #ddd;border-radius:4px}
.card-head{height:27px;background:linear-gradient(var(--navy),var(--navy-dark));border-radius:4px 4px 0 0;color:#fff;font-family:"Cinzel",serif;font-size:11.5px;text-align:center;line-height:27px;letter-spacing:.5px}
.card-media{margin:9px 8px 0;width:162px;height:94px;border:1px solid #ddd}
.card-text{margin:9px 10px 0;font-size:8px;line-height:13px;color:#444}
.card-btn{position:absolute;left:50%;bottom:-1px;transform:translateX(-50%);width:84px;height:16px;background:var(--green-dark);color:#fff;font-size:8px;font-weight:700;text-align:center;line-height:16px;clip-path:polygon(8% 0,92% 0,100% 100%,0 100%)}

/* news */
.news-item{left:83px;width:392px;height:60px}
.news-thumb{position:absolute;left:0;top:0;width:52px;height:58px;border:1px solid #ccc;background:linear-gradient(#e4e4e4,#b7b7b7)}
.news-date{position:absolute;left:63px;top:-2px;font-size:8.5px;font-weight:700;color:#222}
.news-title{position:absolute;left:63px;top:10px;font-size:8.5px;font-weight:700;color:var(--green)}
.news-body{position:absolute;left:63px;top:24px;width:330px;font-size:8px;line-height:12.5px;color:#444}
.news-sep{left:145px;top:940px;width:330px;height:1px;background:#e2e2e2}
.admissions{left:513px;top:862px;list-style:none}
.admissions li{font-size:9.5px;font-weight:700;color:var(--navy);height:22.2px;display:flex;align-items:center;gap:6px}
.vdiv{left:494px;top:836px;width:1px;height:180px;background:var(--line)}

/* footer */
.footer{left:0;top:1036px;width:758px;height:144px;background:var(--footer)}
.footer-col{color:var(--footer-text)}
.footer-bar{left:0;top:1180px;width:758px;height:20px;background:var(--footer-bar);color:#ccc;font-size:7.5px;text-align:center;line-height:20px}
.f-head{font-size:9.5px;color:#eee;display:flex;align-items:center;gap:6px;letter-spacing:.2px}
.f-head::after{content:"";width:22px;height:1px;background:#666}
.quick{list-style:none;font-size:8px}
.quick li{height:19.2px}
.contact-row{display:flex;gap:8px;align-items:flex-start;font-size:7.5px;line-height:11px;color:var(--footer-text)}
.contact-row b{color:#fff}
.nl-input{display:block;width:136px;height:16px;background:#fff;border:0;font-size:7.5px;padding-left:5px;color:#888;font-family:"Lato",sans-serif}
.nl-btn{background:var(--green);color:#fff;font-size:8px;font-weight:700;width:56px;height:16px;text-align:center;line-height:16px}
.soc{display:flex;gap:5px;align-items:center;height:25px}
.soc .dot{width:23px;height:23px;border-radius:50%;flex:none}
.soc b{font-family:"Lora",serif;font-weight:400;font-size:9.5px;line-height:11px;display:block;color:#eee}
.soc small{display:block;font-size:6.5px;line-height:8px;color:#999;letter-spacing:.4px}
</style>
</head>
<body>

<header class="site-header abs"></header>
<nav class="utility-tabs abs"><a>APPLY TODAY</a><a>DONATE</a><a>LIBRARY</a><a>TEXT FOR INFO</a></nav>
<div class="brand abs">CEDARVALE<br>RIDGE<br>COLLEGE</div>
<div class="social-dots abs"><span></span><span></span><span></span><span></span></div>
<form class="search abs"><input placeholder="Search here......"><button type="button" aria-label="Search"><svg width="10" height="10" viewBox="0 0 10 10"><circle cx="4" cy="4" r="3" fill="none" stroke="#fff" stroke-width="1.4"/><line x1="6.2" y1="6.2" x2="9" y2="9" stroke="#fff" stroke-width="1.6"/></svg></button></form>

<nav class="main-nav abs">
  <div class="main-nav-links">
    <a class="active">Home</a><a>About Us</a><a>Consider Cedarvale</a><a>Current Students</a><a>Alumni</a><a>Supporters</a><a>News &amp; Events</a><a>Cedarvale Park</a><a>Contact</a>
  </div>
</nav>

<div class="hero abs" role="img" aria-label="Campus buildings lit at dusk with parking lot and trees"></div>
<div class="hero-arrow abs" style="left:0"><svg width="10" height="12"><path d="M8 1 3 6l5 5" stroke="#fff" stroke-width="2.2" fill="none"/></svg></div>
<div class="hero-arrow abs" style="left:720px"><svg width="10" height="12"><path d="M2 1l5 5-5 5" stroke="#fff" stroke-width="2.2" fill="none"/></svg></div>
<div class="hero-caption abs">Educating, equipping and enriching Christians for spirit-empowered ministry in the church and in the world</div>

<h2 class="heading abs" style="left:84px;top:376px">ABOUT <em>CEDARVALE RIDGE COLLEGE</em></h2>
<div class="heading-rule abs" style="left:84px;top:397px;width:334px"></div>
<div class="about-copy abs">
  <p>Lorem ipsum dolor sit amet, consectetur adipiscing elit. Aenean et dignissim sem, interdum risus. Vestibulum consectetur nisi mollis diam pulvinar adipiscing. Vestibulum ut urna nec nibh adipiscing facilisis. Etiam auctor porta lacus ac luctus. Praesent ac libero fermentum, rhoncus magna a, dapibus mauris. Nam ut auctor justo. Sed ante odio, luctus quis nequ nec, adipiscing eleifend arcu. Integer nunc turpis, porttitor at lorem ut.</p>
  <p>Quisque hendrerit molestie commodo. Aliquam imperdiet varius tortor ut condiment Nulla ornare ultricies nunc et scelerisque. Class aptent taciti sociosqu ad litora torquent conubia nostra, per inceptos himenaeos. Mauris mattis ultrices diam nec luctus.</p>
</div>
<a class="read-more-link abs">READ MORE</a>
<div class="divider abs"></div>

<h2 class="heading abs" style="left:469px;top:376px">LATEST <em>VIDEOS</em></h2>
<div class="heading-rule abs" style="left:469px;top:397px;width:206px"></div>
<div class="video abs" role="img" aria-label="Video still of a congregation gathered in an auditorium"></div>
<div class="video-bar abs"><svg width="6" height="7"><rect width="2" height="7" fill="#ddd"/><rect x="4" width="2" height="7" fill="#ddd"/></svg><div class="track"><i></i></div><svg width="30" height="6"><rect y="2" width="30" height="2" fill="#666"/><circle cx="18" cy="3" r="3" fill="#eee"/></svg></div>

<section class="campus abs"></section>
<div class="campus-title abs"><span class="line"></span><h2 class="heading">OUR CAMPUS</h2><span class="line"></span></div>

<article class="card abs" style="left:83px">
  <div class="card-head">PHOTO TOUR</div>
  <div class="card-media" style="background:linear-gradient(#d8d2c6,#7a6a5a)" role="img" aria-label="Lecturer speaking to a classroom of students"></div>
  <p class="card-text">Lorem ipsum dolor sit amet, consectetuero adipiscing elit, sed diam nonummy nibhnou euismod tincidunt ut laoreet dolore into.</p>
  <div class="card-btn">READ MORE</div>
</article>
<article class="card abs" style="left:289px">
  <div class="card-head">CAMPUS MAP</div>
  <div class="card-media" style="background:linear-gradient(135deg,#4d6b48,#8a6a5c)" role="img" aria-label="Aerial campus map with location markers"></div>
  <p class="card-text">Lorem ipsum dolor sit amet, consectetuero adipiscing elit, sed diam nonummy nibhnou euismod tincidunt ut laoreet dolore into.</p>
  <div class="card-btn">READ MORE</div>
</article>
<article class="card abs" style="left:497px">
  <div class="card-head">MAP &amp; DIRECTION</div>
  <div class="card-media" style="background:linear-gradient(135deg,#dfe6d2,#c9d8bd)" role="img" aria-label="Street map showing the college location"></div>
  <p class="card-text">Lorem ipsum dolor sit amet, consectetuero adipiscing elit, sed diam nonummy nibhnou euismod tincidunt ut laoreet dolore into.</p>
  <div class="card-btn">READ MORE</div>
</article>

<h2 class="heading abs" style="left:85px;top:835px">RECENT <em>NEWS &amp; EVENTS</em></h2>
<div class="heading-rule abs" style="left:85px;top:856px;width:390px"></div>
<div class="news-item abs" style="top:871px">
  <div class="news-thumb" role="img" aria-label="Portrait photo"></div>
  <div class="news-date">03 May, 2014</div>
  <div class="news-title">LOREM IPSUM DOLOR SIT AMNSECTETUR</div>
  <p class="news-body">Lorem ipsum dolor sit amet, consectetur adipiscing elit. Pellentesque id erat in mag mattis fermentum non eu ligula. Nunc mattis, arcu sed vehicula vestibulum, purus mauris egestas dolor, eget sagittis eros magna eget magna. Nulla tempus, libero ornare auctor.</p>
</div>
<div class="news-sep abs"></div>
<div class="news-item abs" style="top:954px">
  <div class="news-thumb" role="img" aria-label="Portrait photo"></div>
  <div class="news-date">03 May, 2014</div>
  <div class="news-title">LOREM IPSUM DOLOR SIT AMNSECTETUR</div>
  <p class="news-body">Lorem ipsum dolor sit amet, consectetur adipiscing elit. Pellentesque id erat in mag mattis fermentum non eu ligula. Nunc mattis, arcu sed vehicula vestibulum, purus mauris egestas dolor, eget sagittis eros magna eget magna. Nulla tempus, libero ornare auctor.</p>
</div>
<div class="vdiv abs"></div>

<h2 class="heading abs" style="left:513px;top:835px">OUR <em>ADMISSIONS</em></h2>
<div class="heading-rule abs" style="left:513px;top:856px;width:162px"></div>
<ul class="admissions abs">
  <li><svg width="8" height="8"><path d="M0 0l3.5 4L0 8zM4 0l3.5 4L4 8z" fill="var(--green)"/></svg>Download The Full Catalogue</li>
  <li><svg width="8" height="8"><path d="M0 0l3.5 4L0 8zM4 0l3.5 4L4 8z" fill="var(--green)"/></svg>Apply Today (Application Package)</li>
  <li><svg width="8" height="8"><path d="M0 0l3.5 4L0 8zM4 0l3.5 4L4 8z" fill="var(--green)"/></svg>Information Request</li>
  <li><svg width="8" height="8"><path d="M0 0l3.5 4L0 8zM4 0l3.5 4L4 8z" fill="var(--green)"/></svg>Browse our Programs</li>
  <li><svg width="8" height="8"><path d="M0 0l3.5 4L0 8zM4 0l3.5 4L4 8z" fill="var(--green)"/></svg>Download Forms</li>
  <li><svg width="8" height="8"><path d="M0 0l3.5 4L0 8zM4 0l3.5 4L4 8z" fill="var(--green)"/></svg>Admissions Information</li>
  <li><svg width="8" height="8"><path d="M0 0l3.5 4L0 8zM4 0l3.5 4L4 8z" fill="var(--green)"/></svg>Campus Directory</li>
</ul>

<footer class="footer abs"></footer>
<div class="footer-col abs" style="left:83px;top:1054px">
  <div class="f-head">QUICK LINK</div>
  <ul class="quick" style="margin-top:12px"><li>Home</li><li>Services</li><li>Library</li><li>News</li><li>Contact Us</li></ul>
</div>
<div class="footer-col abs" style="left:200px;top:1054px;width:160px">
  <div class="f-head">CONTACT ADDRESS</div>
  <div class="contact-row" style="margin-top:12px"><svg width="9" height="13" style="flex:none"><path d="M4.5 0a4.5 4.5 0 0 1 4.5 4.5C9 8 4.5 13 4.5 13S0 8 0 4.5A4.5 4.5 0 0 1 4.5 0z" fill="#eee"/><circle cx="4.5" cy="4.5" r="1.7" fill="#262626"/></svg><div><b>CEDARVALE office is located at:</b><br>4810 Alder Bend Road, Fernhollow,<br>BC V4K 2R8</div></div>
  <div class="contact-row" style="margin-top:9px;font-size:9px"><svg width="9" height="11" style="flex:none"><rect x="1" width="7" height="11" rx="1.5" fill="#eee"/><rect x="2.5" y="1.5" width="4" height="6" fill="#262626"/></svg>1-800-555-0142</div>
  <div class="contact-row" style="margin-top:8px;font-size:9px"><svg width="10" height="10" style="flex:none"><rect y="3" width="10" height="5" fill="#eee"/><rect x="2" width="6" height="3" fill="#eee"/><rect x="2" y="7" width="6" height="3" fill="#bbb"/></svg>(604) 555-0187</div>
  <div class="contact-row" style="margin-top:8px"><svg width="10" height="9" style="flex:none"><path d="M0 3l5-3 5 3v6H0z" fill="#eee"/><path d="M0 3l5 3 5-3" stroke="#262626" fill="none"/></svg>pr@cedarvaleridge.ca</div>
</div>
<div class="footer-col abs" style="left:383px;top:1054px;width:140px">
  <div class="f-head">NEWSLETTER SIGNUP</div>
  <p style="font-size:7.5px;line-height:11px;margin-top:10px">Signup with us and get update in your inbox.</p>
  <input class="nl-input" style="margin-top:5px" placeholder="Your Name">
  <input class="nl-input" style="margin-top:6px" placeholder="Email address">
  <div class="nl-btn" style="margin-top:6px">Subscribe</div>
</div>
<div class="footer-col abs" style="left:569px;top:1054px">
  <div class="f-head">SOCIAL CONNECT</div>
  <div class="soc" style="margin-top:10px"><span class="dot" style="background:#3b5a9a"></span><div><b>COMMUNITY PAGE</b><small>BECOME A FAN</small></div></div>
  <div class="soc" style="margin-top:6px"><span class="dot" style="background:#d5452f"></span><div><b>CIRCLE NETWORK</b><small>ADD TO CIRCLES</small></div></div>
  <div class="soc" style="margin-top:6px"><span class="dot" style="background:#f08a24"></span><div><b>RSS FEED</b><small>SUBSCRIBE NOW</small></div></div>
</div>
<div class="footer-bar abs">Copyright 2014, CEDARVALE. All rights reserved.</div>

</body>
</html>
```